Business Card Design for a Software Startup

We'd like to have a business card design. We already have a logo. Basically what we need is a clean design with name, address, cellphone and phone numbers, e-mail and web site address (front) and a space on the back with our logo with the company name on the right side and some texts on the bottom.
We are a development and consulting company in Brazil with highly qualified team of professionals in Java, iOS and Android development and consulting.

Target Market(s)

CIO, IT managers of mid to big size companies

Industry/Entity Type

Business

```html
<!DOCTYPE html>
<html lang="en">
<head>
<meta charset="UTF-8">
<title>VORTIQ Business Card</title>
<link href="https://fonts.googleapis.com/css2?family=Jost:wght@400;500;700&display=swap" rel="stylesheet">
<style>
  :root {
    --stage: #e9ebee;
    --card: #ffffff;
    --navy: #143a6b;
    --brand-blue: #15427a;
    --sky: #2aa6e0;
    --mark-top: #1b4f86;
    --mark-bottom: #1d8ccc;
    --ink: #3a3d42;
    --muted: #6b6f75;
    --divider: #d9dde2;
  }
  * { box-sizing: border-box; margin: 0; padding: 0; }
  html, body { width: 1200px; height: 720px; overflow: hidden; }
  body {
    background: var(--stage);
    font-family: "Jost", "Futura", sans-serif;
    color: var(--ink);
    position: relative;
  }
  .card {
    position: absolute;
    top: 205px;
    width: 540px;
    height: 310px;
    background: var(--card);
    box-shadow: 0 6px 20px rgba(20, 40, 70, 0.15);
    overflow: hidden;
  }
  .card--front { left: 40px; }
  .card--back { left: 620px; }

  /* Front */
  .brand-block {
    position: absolute;
    left: 50px;
    top: 56px;
    width: 160px;
    display: flex;
    flex-direction: column;
    align-items: center;
    gap: 14px;
  }
  .brand-square {
    width: 88px;
    height: 88px;
    border-radius: 14px;
    background: linear-gradient(160deg, var(--mark-top), var(--mark-bottom));
  }
  .brand-name {
    font-weight: 700;
    color: var(--brand-blue);
    font-size: 34px;
    letter-spacing: 1px;
    line-height: 1;
  }
  .divider {
    position: absolute;
    left: 248px;
    top: 40px;
    width: 1px;
    height: 180px;
    background: var(--divider);
  }
  .contact {
    position: absolute;
    left: 268px;
    top: 42px;
  }
  .contact__name {
    font-weight: 700;
    font-size: 22px;
    color: var(--brand-blue);
    line-height: 1.1;
  }
  .contact__title {
    font-size: 15px;
    color: var(--muted);
    margin-bottom: 10px;
  }
  .contact__list { list-style: none; }
  .contact__item {
    display: flex;
    align-items: center;
    gap: 9px;
    font-size: 14.5px;
    line-height: 25px;
  }
  .contact__icon { width: 13px; height: 13px; fill: var(--ink); flex: none; }
  .band-line {
    position: absolute;
    left: 0; right: 0;
    bottom: 44px;
    height: 3px;
    background: var(--sky);
  }
  .band {
    position: absolute;
    left: 0; right: 0; bottom: 0;
    height: 40px;
    background: var(--navy);
    color: #fff;
    font-size: 15px;
    letter-spacing: 0.3px;
    display: flex;
    align-items: center;
    justify-content: center;
  }

  /* Back */
  .back-brand {
    position: absolute;
    left: 0; right: 0;
    top: 70px;
    display: flex;
    align-items: center;
    justify-content: center;
    gap: 20px;
  }
  .back-brand .brand-square { width: 120px; height: 120px; border-radius: 18px; }
  .back-brand .brand-name { font-size: 40px; }
  .back-web {
    position: absolute;
    right: 60px;
    bottom: 48px;
    font-size: 19px;
    font-weight: 500;
    letter-spacing: 6px;
    color: var(--ink);
  }
</style>
</head>
<body>

  <section class="card card--front" aria-label="Business card front">
    <div class="brand-block">
      <div class="brand-square"></div>
      <div class="brand-name">VORTIQ</div>
    </div>
    <div class="divider"></div>
    <div class="contact">
      <p class="contact__name">Your Name</p>
      <p class="contact__title">Title</p>
      <ul class="contact__list">
        <li class="contact__item">
          <svg class="contact__icon" viewBox="0 0 16 16"><path d="M3 1h3l1.5 4-2 1.3a9 9 0 0 0 4.2 4.2L11 8.5l4 1.5v3a2 2 0 0 1-2 2A12 12 0 0 1 1 3a2 2 0 0 1 2-2z"/></svg>
          555-010-2846
        </li>
        <li class="contact__item">
          <svg class="contact__icon" viewBox="0 0 16 16"><path d="M5 0h6a1.5 1.5 0 0 1 1.5 1.5v13A1.5 1.5 0 0 1 11 16H5a1.5 1.5 0 0 1-1.5-1.5v-13A1.5 1.5 0 0 1 5 0zm0 2v10h6V2zm3 11a1 1 0 1 0 0 2 1 1 0 0 0 0-2z"/></svg>
          555-017-6392
        </li>
        <li class="contact__item">
          <svg class="contact__icon" viewBox="0 0 16 16"><path d="M1 3h14v10H1zm1.5 1.5v.4L8 9l5.5-4.1v-.4zm0 2.3v4.7h11V6.8L8 11z"/></svg>
          yourname@vortiq.com
        </li>
        <li class="contact__item">
          <svg class="contact__icon" viewBox="0 0 16 16"><circle cx="8" cy="8" r="7"/></svg>
          www.vortiq.com
        </li>
      </ul>
    </div>
    <div class="band-line"></div>
    <div class="band">Door No. Street Name City Name, State, Zip Code.</div>
  </section>

  <section class="card card--back" aria-label="Business card back">
    <div class="back-brand">
      <div class="brand-square"></div>
      <div class="brand-name">VORTIQ</div>
    </div>
    <p class="back-web">www.vortiq.com</p>
  </section>

</body>
</html>
```